Consulting Company PowerPoint Template Design

We are looking for an updated PowerPoint template design or our 55 person energy consulting firm (K7) based in San Francisco (www.kseven-example.com). We would like two versions of the same PowerPoint template in a 16:9 and 4:3 format with our existing logo.

We have an existing color scheme and template and are seeking your help to polish/update the template design for wide format and create a flexible template that is easy to use with content from Excel and Word. Our current template, and a couple of examples that we like are attached.

Specific requests include:

• Dark background for slide title
• A narrow section header
• Maximizing white space for content
• A limited number of well designed Master template layouts to choose from
• A selection of title and section header slides that are not San Francisco specific with some variety to chose from ideally with a focus on energy or nature, graphics/visuals.

For examples of energy specific templates see:
https://www.brightslidehub.example/energy/powerpoint-templates/0.html

Requirements
Must have
• Must use our logo but open to other designs, fonts, and styles for the PowerPoint template.
• Please use our existing color scheme found in the attached Excel file.
• Also we would like the ability to easily copy and paste from our existing/original template to the new template. In other words we would like backward compatibility to apply the new template format to our old PowerPoints that use our existing template.

```html
<!DOCTYPE html>
<html lang="en">
<head>
<meta charset="utf-8">
<title>Our Graphs Chart</title>
<link href="https://fonts.googleapis.com/css2?family=Titillium+Web:wght@400;600;700&display=swap" rel="stylesheet">
<style>
  :root {
    --brand-teal: #0b4f6c;
    --brand-gold: #d6b76c;
    --text-dark: #222222;
    --axis-text: #5a5a5a;
    --value-text: #666666;
    --grid: #e9e9e9;
    --bg: #ffffff;
    --green: #7cb342;  --green-lt: #b5d49a;
    --blue: #3a8fdc;   --blue-lt: #8cbeeb;
    --slate: #465567;  --slate-lt: #8796aa;
    --orange: #f39a2e; --orange-lt: #f8c386;
    --red: #e8263f;    --red-lt: #f07b8a;
    --grey: #a0a0a0;   --grey-lt: #c6c6c6;
  }
  html, body { margin: 0; padding: 0; overflow: hidden; background: var(--bg); }
  .slide {
    position: relative; width: 1200px; height: 900px; overflow: hidden;
    background: var(--bg); font-family: "Titillium Web", Arial, sans-serif;
  }
  .title-accent { position: absolute; left: 0; top: 21px; width: 12px; height: 66px; background: var(--brand-gold); }
  .slide-title {
    position: absolute; left: 26px; top: 22px; margin: 0;
    font-size: 40px; font-weight: 600; line-height: 60px; color: var(--brand-teal);
  }
  .brand { position: absolute; right: 18px; top: 12px; display: flex; align-items: center; gap: 12px; }
  .brand-name { font-size: 30px; font-weight: 700; color: var(--brand-teal); }
  .brand-dot { width: 72px; height: 72px; border-radius: 50%; background: var(--brand-teal); }
  .chart { position: absolute; left: 0; top: 0; width: 1200px; height: 900px; }
  .chart .grid line { stroke: var(--grid); stroke-width: 0.8; }
  .chart .axis-label { font-size: 14px; fill: var(--axis-text); text-anchor: end; font-family: "Titillium Web", Arial, sans-serif; }
  .chart .month-label { font-size: 14.5px; fill: var(--axis-text); text-anchor: middle; font-family: "Titillium Web", Arial, sans-serif; }
  .chart .value-label { font-size: 8.5px; fill: var(--value-text); text-anchor: middle; font-family: "Titillium Web", Arial, sans-serif; }
  .slide-body {
    position: absolute; left: 63px; top: 686px; width: 1060px; margin: 0;
    font-size: 18.5px; line-height: 32px; color: var(--text-dark);
  }
  .footer { position: absolute; left: 0; bottom: 0; width: 1200px; height: 45px; background: var(--brand-teal); }
  .footer-name { position: absolute; left: 12px; top: 0; line-height: 45px; font-size: 21px; font-weight: 700; color: #fff; }
  .footer-tab { position: absolute; right: 0; bottom: 0; width: 100px; height: 45px; }
  .page-number { position: absolute; right: 26px; bottom: 0; line-height: 45px; font-size: 24px; color: #fff; }
</style>
</head>
<body>
<div class="slide">
  <div class="title-accent"></div>
  <h1 class="slide-title">Our Graphs Chart</h1>
  <div class="brand"><span class="brand-name">K7</span><span class="brand-dot"></span></div>

  <svg class="chart" viewBox="0 0 800 600" aria-label="Monthly paired bar chart">
    <g class="grid">
      <line x1="78" y1="155.2" x2="735" y2="155.2"/>
      <line x1="78" y1="194" x2="735" y2="194"/>
      <line x1="78" y1="232.8" x2="735" y2="232.8"/>
      <line x1="78" y1="271.6" x2="735" y2="271.6"/>
      <line x1="78" y1="310.4" x2="735" y2="310.4"/>
      <line x1="78" y1="349.2" x2="735" y2="349.2"/>
      <line x1="78" y1="388" x2="735" y2="388"/>
    </g>
    <g>
      <text class="axis-label" x="61" y="160">120</text>
      <text class="axis-label" x="61" y="199">100</text>
      <text class="axis-label" x="61" y="238">80</text>
      <text class="axis-label" x="61" y="277">60</text>
      <text class="axis-label" x="61" y="315">40</text>
      <text class="axis-label" x="61" y="354">20</text>
      <text class="axis-label" x="61" y="393">0</text>
    </g>
    <g class="bars">
      <rect x="90" y="194" width="15" height="194" fill="var(--green)"/>
      <rect x="108" y="213.4" width="15" height="174.6" fill="var(--green-lt)"/>
      <rect x="144.3" y="213.4" width="15" height="174.6" fill="var(--blue)"/>
      <rect x="162.3" y="232.8" width="15" height="155.2" fill="var(--blue-lt)"/>
      <rect x="198.6" y="291" width="15" height="97" fill="var(--slate)"/>
      <rect x="216.6" y="194" width="15" height="194" fill="var(--slate-lt)"/>
      <rect x="252.9" y="194" width="15" height="194" fill="var(--orange)"/>
      <rect x="270.9" y="271.6" width="15" height="116.4" fill="var(--orange-lt)"/>
      <rect x="307.2" y="194" width="15" height="194" fill="var(--red)"/>
      <rect x="325.2" y="213.4" width="15" height="174.6" fill="var(--red-lt)"/>
      <rect x="361.5" y="271.6" width="15" height="116.4" fill="var(--grey)"/>
      <rect x="379.5" y="242.5" width="15" height="145.5" fill="var(--grey-lt)"/>
      <rect x="415.8" y="291" width="15" height="97" fill="var(--green)"/>
      <rect x="433.8" y="194" width="15" height="194" fill="var(--green-lt)"/>
      <rect x="470.1" y="232.8" width="15" height="155.2" fill="var(--blue)"/>
      <rect x="488.1" y="261.9" width="15" height="126.1" fill="var(--blue-lt)"/>
      <rect x="524.4" y="329.8" width="15" height="58.2" fill="var(--slate)"/>
      <rect x="542.4" y="213.4" width="15" height="174.6" fill="var(--slate-lt)"/>
      <rect x="578.7" y="252.2" width="15" height="135.8" fill="var(--orange)"/>
      <rect x="596.7" y="232.8" width="15" height="155.2" fill="var(--orange-lt)"/>
      <rect x="633" y="194" width="15" height="194" fill="var(--red)"/>
      <rect x="651" y="194" width="15" height="194" fill="var(--red-lt)"/>
      <rect x="687.3" y="291" width="15" height="97" fill="var(--grey)"/>
      <rect x="705.3" y="194" width="15" height="194" fill="var(--grey-lt)"/>
    </g>
    <g>
      <text class="value-label" x="97.5" y="184">100</text>
      <text class="value-label" x="115.5" y="203">90</text>
      <text class="value-label" x="151.8" y="203">90</text>
      <text class="value-label" x="169.8" y="223">80</text>
      <text class="value-label" x="206.1" y="281">50</text>
      <text class="value-label" x="224.1" y="184">100</text>
      <text class="value-label" x="260.4" y="184">100</text>
      <text class="value-label" x="278.4" y="262">60</text>
      <text class="value-label" x="314.7" y="184">100</text>
      <text class="value-label" x="332.7" y="203">90</text>
      <text class="value-label" x="369" y="262">60</text>
      <text class="value-label" x="387" y="233">75</text>
      <text class="value-label" x="423.3" y="281">50</text>
      <text class="value-label" x="441.3" y="184">100</text>
      <text class="value-label" x="477.6" y="223">80</text>
      <text class="value-label" x="495.6" y="252">65</text>
      <text class="value-label" x="531.9" y="320">30</text>
      <text class="value-label" x="549.9" y="203">90</text>
      <text class="value-label" x="586.2" y="242">70</text>
      <text class="value-label" x="604.2" y="223">80</text>
      <text class="value-label" x="640.5" y="184">100</text>
      <text class="value-label" x="658.5" y="184">100</text>
      <text class="value-label" x="694.8" y="281">50</text>
      <text class="value-label" x="712.8" y="184">100</text>
    </g>
    <g>
      <text class="month-label" x="106.5" y="425">Jan</text>
      <text class="month-label" x="160.8" y="425">Feb</text>
      <text class="month-label" x="215.1" y="425">Mar</text>
      <text class="month-label" x="269.4" y="425">Apr</text>
      <text class="month-label" x="323.7" y="425">May</text>
      <text class="month-label" x="378" y="425">Jun</text>
      <text class="month-label" x="432.3" y="425">Jul</text>
      <text class="month-label" x="486.6" y="425">Aug</text>
      <text class="month-label" x="540.9" y="425">Sep</text>
      <text class="month-label" x="595.2" y="425">Act</text>
      <text class="month-label" x="649.5" y="425">Nov</text>
      <text class="month-label" x="703.8" y="425">Dec</text>
    </g>
  </svg>

  <p class="slide-body">Lorem ipsum dolor sit Lorem ipsum dolor sit&nbsp; Lorem ipsum dolor sit Lorem ipsum dolor sit&nbsp; Lorem ipsum dolor sit Lorem ipsum dolor sit&nbsp; Lorem ipsum dolor sit Lorem ipsum dolor sit&nbsp; Lorem ipsum dolor sit Lorem ipsum dolor sit&nbsp; Lorem ipsum dolor sit Lorem ipsum dolor sit&nbsp; Lorem ipsum dolor sit Lorem ipsum dolor sit</p>

  <div class="footer">
    <span class="footer-name">Kestrel Seven Energy Advisors</span>
    <svg class="footer-tab" viewBox="0 0 100 45" aria-hidden="true">
      <polygon points="10,0 100,0 100,45 20,45 4,22" fill="#ffffff"/>
      <polygon points="16,0 100,0 100,45 26,45 10,22" fill="var(--brand-gold)"/>
    </svg>
    <span class="page-number">1</span>
  </div>
</div>
</body>
</html>
```